Business Card Design for Software Development Company

I am looking for a business card design the incorporates my new logo (attached below).

Key information to include:
Name: Martin Quelbrook
Title: CEO
Email: martin@brightwellcivic.example
Phone: 555-218-9403
Website: www.brightwellcivic.example

NOTE: This design should be easy to edit so that we can order cards for different members of our team.

```html
<!DOCTYPE html>
<html lang="en">
<head>
<meta charset="utf-8">
<title>Brightwell Labs – Business Card</title>
<link rel="stylesheet" href="https://fonts.googleapis.com/css2?family=Figtree:wght@400;500;700&display=swap">
<style>
  :root {
    --stage: #1c1c1c;
    --card-light: #f4f4f4;
    --card-dark: #1f1f1f;
    --ink: #222222;
    --teal: #15a58f;
    --orange: #e8782a;
    --muted-mark: #5c5c5c;
    --muted-tagline: #333333;
    --tint: rgba(21,165,143,0.09);
  }
  * { margin: 0; padding: 0; box-sizing: border-box; }
  html, body { width: 1200px; height: 1059px; overflow: hidden; background: var(--stage); }
  body { position: relative; font-family: "Figtree", sans-serif; color: var(--ink); }

  .card { position: absolute; border-radius: 22px; overflow: hidden; }
  .card--front { left: 257px; top: 89px; width: 687px; height: 390px; background: var(--card-light); }
  .card--back  { left: 254px; top: 547px; width: 693px; height: 393px; background: var(--card-dark); }

  .brand { position: absolute; display: flex; align-items: center; gap: 10px; white-space: nowrap; }
  .brand__square { width: 26px; height: 26px; background: var(--teal); flex: none; }
  .brand__name { font-weight: 700; font-size: 38px; letter-spacing: -0.5px; line-height: 1; white-space: nowrap; }
  .brand__tagline { position: absolute; right: 0; font-size: 5.5px; font-weight: 700; letter-spacing: 0.3px; white-space: nowrap; }

  .card--front .brand { left: 37px; top: 67px; }
  .card--front .brand__name { color: var(--ink); }
  .card--front .brand__tagline { top: 42px; color: var(--ink); }

  .person { position: absolute; right: 35px; top: 64px; text-align: right; white-space: nowrap; }
  .person__name { font-weight: 700; font-size: 25px; line-height: 1.1; }
  .person__first { color: var(--teal); }
  .person__last { color: var(--orange); }
  .person__title { font-size: 18px; font-weight: 400; margin-top: 2px; }

  .tab { position: absolute; right: 0; top: 68px; width: 18px; height: 40px; background: var(--teal); border-radius: 5px 0 0 5px; }

  .accent-block { position: absolute; right: 0; bottom: 0; width: 250px; height: 205px;
    background: linear-gradient(160deg, var(--tint), rgba(232,120,42,0.06)); }

  .address { position: absolute; left: 37px; top: 199px; font-size: 18px; line-height: 24px; white-space: nowrap; }
  .contacts { position: absolute; left: 37px; top: 264px; list-style: none; }
  .contacts li { display: flex; align-items: center; gap: 8px; font-size: 18px; height: 33px; white-space: nowrap; }
  .contacts svg { width: 15px; height: 15px; flex: none; }

  .card--back .brand { left: 50%; top: 198px; transform: translate(-50%, -50%); gap: 12px; }
  .card--back .brand__square { width: 40px; height: 40px; }
  .card--back .brand__name { font-size: 66px; letter-spacing: -0.8px; color: var(--muted-mark); }
  .card--back .brand__tagline { top: 66px; font-size: 8.5px; color: var(--muted-tagline); }
</style>
</head>
<body>
  <section class="card card--front">
    <div class="accent-block"></div>
    <div class="brand">
      <span class="brand__square"></span>
      <span class="brand__name">Brightwell Labs</span>
      <span class="brand__tagline">A DIVISION OF BRIGHTWELL CIVIC</span>
    </div>
    <div class="person">
      <p class="person__name"><span class="person__first">Martin</span> <span class="person__last">Quelbrook</span></p>
      <p class="person__title">CEO</p>
    </div>
    <span class="tab"></span>
    <p class="address">1280 Harbor Point Rd, Fairview<br>VA 20000, USA</p>
    <ul class="contacts">
      <li>
        <svg viewBox="0 0 16 16" aria-hidden="true"><path fill="#f0b88a" d="M2 5c0-2 2-3 6-3s6 1 6 3v1h-3V5H5v1H2z M4 7h8l2 6H2z"/></svg>
        555-218-9403
      </li>
      <li>
        <svg viewBox="0 0 16 16" aria-hidden="true"><path fill="var(--teal)" d="M1 6l7-5 7 5v9H1z"/><path fill="#fff" d="M2 7l6 4 6-4v1l-6 4-6-4z"/></svg>
        martin@brightwellcivic.example
      </li>
      <li>
        <svg viewBox="0 0 16 16" aria-hidden="true"><circle cx="8" cy="8" r="7" fill="var(--orange)"/><path fill="#fff" d="M5 4c2 0 3 1 2 3s-2 1-3 0zM9 9c2 0 3 1 2 3l-2 1z"/></svg>
        www.brightwellcivic.example
      </li>
    </ul>
  </section>

  <section class="card card--back">
    <div class="brand">
      <span class="brand__square"></span>
      <span class="brand__name">Brightwell Labs</span>
      <span class="brand__tagline">A DIVISION OF BRIGHTWELL CIVIC</span>
    </div>
  </section>
</body>
</html>
```